FinTech company looking to revamp and expand client-facing interface for our financial models

Pellworth Engines currently has a very simple website that allows clients to interact with our financial models. We are looking to completely redesign the current site and add several extra pages to provide extra functionality. We want the design to have a modern, slick feel, that will work on both a desktop or a tablet. It should be straightforward for clients to move between different pages at any time, and clear from the layout how to interact with the more advanced features. We have included screenshots of existing pages in the attached design brief, as well as sketches of the functionality required by the new pages, but can't provide a direct link to the current site.
Target Market(s)
Professional investors that will be paying to access the interface
Industry/Entity Type
Finance
Number of Pages Required
4 page
Colors
Designer to choose colors to be used in the design.
Look and feel
Each slider illustrates characteristics of the customer's brand and the style your logo design should communicate.

```html
<!DOCTYPE html>
<html lang="en">
<head>
<meta charset="utf-8">
<title>Pellworth Engines – ETF Pairs</title>
<link rel="stylesheet" href="https://fonts.googleapis.com/css2?family=Open+Sans:wght@600;700&family=Roboto:wght@500;700&family=Roboto+Condensed:wght@400&display=swap">
<style>
:root{
  --page:#e6e6e6;
  --white:#ffffff;
  --navy:#0b3768;
  --ink:#1b1b1b;
  --teal:#006b63;
  --row-alt:#efefef;
  --rule:#dcdcdc;
}
*{box-sizing:border-box;margin:0;padding:0}
html,body{width:1200px;height:706px;overflow:hidden;background:var(--page)}
.stage{position:absolute;left:0;top:0;width:1300px;height:765px;transform:scale(0.9231,0.9229);transform-origin:0 0;font-family:"Open Sans",sans-serif;color:var(--ink)}
.panel{position:absolute;left:15px;top:15px;width:1270px;height:735px;background:linear-gradient(#ececec 0,#e9e9e9 160px,#e2e2e2 200px,#f4f4f4 520px,#fafafa 735px)}
.topbar{position:absolute;left:15px;top:15px;width:1270px;height:60px;background:var(--white);display:flex;box-shadow:0 6px 14px rgba(0,0,0,.08)}
.brand{width:180px;font:700 19px "Open Sans",sans-serif;line-height:60px;padding-left:50px;white-space:nowrap}
.range{width:90px;text-align:center;font:700 14px "Open Sans",sans-serif;line-height:60px;border-right:1px solid #e4e4e4}
.range.active{background:var(--navy);color:var(--white)}
.spacer{flex:1}
.nav{display:flex;align-items:center;justify-content:center;gap:8px;font:700 13px "Open Sans",sans-serif;border-left:1px solid #e4e4e4}
.nav.active{background:var(--navy);color:var(--white)}
.nav svg{width:24px;height:24px}
.tab{position:absolute;background:var(--white);font:700 13px "Open Sans",sans-serif;color:#555;text-align:center;border-radius:4px 4px 0 0;box-shadow:0 -2px 6px rgba(0,0,0,.05)}
.tab.active{background:var(--ink);color:var(--white)}
.tab.add{background:var(--navy);color:var(--white);display:flex;align-items:center;justify-content:center;gap:8px;font-size:14px}
.export{position:absolute;left:1164px;top:212px;display:flex;align-items:center;gap:8px;font:700 17px "Open Sans",sans-serif;color:var(--navy)}
.filters{position:absolute;left:15px;top:335px;width:50px;height:250px;background:var(--ink);border-radius:0 6px 6px 0}
.filters span{position:absolute;left:25px;top:125px;transform:translate(-50%,-50%) rotate(-90deg);color:var(--white);font:700 16px "Open Sans",sans-serif;letter-spacing:1px;white-space:nowrap}
.filters-arrow{position:absolute;left:50px;top:446px}
.grid{position:absolute;left:105px;top:250px;width:1160px;border-collapse:collapse;border-radius:8px;overflow:hidden;box-shadow:0 4px 12px rgba(0,0,0,.12);table-layout:fixed;background:var(--white)}
.grid th{height:70px;font:500 17px Roboto,sans-serif;color:var(--white);border-right:1px solid rgba(255,255,255,.15)}
.grid th.key{background:var(--ink);border-right:1px solid #3a3a3a}
.grid th.stat{background:var(--teal)}
.grid td{height:70px;font:400 17px "Roboto Condensed",sans-serif;color:#111;text-align:center;border-right:1px solid var(--rule);line-height:21px}
.grid td.sector{text-align:left;padding-left:24px}
.grid td.num{text-align:left;padding-left:9px}
.grid tr:nth-child(even) td{background:var(--row-alt)}
.grid td:last-child,.grid th:last-child{border-right:none}
</style>
</head>
<body>
<div class="stage">
  <div class="panel"></div>

  <header class="topbar">
    <div class="brand">Pellworth</div>
    <div class="range active">250D</div>
    <div class="range">83D</div>
    <div class="range">42D</div>
    <div class="spacer"></div>
    <div class="nav active" style="width:141px">
      <svg viewBox="0 0 24 24" fill="none" stroke="#fff" stroke-width="2"><path d="M3 11 12 3l9 8M5 10v10h5v-6h4v6h5V10"/></svg>MODELS</div>
    <div class="nav" style="width:177px">
      <svg viewBox="0 0 24 24" fill="#222"><circle cx="12" cy="12" r="3"/><g fill="none" stroke="#222" stroke-width="1.6"><circle cx="12" cy="12" r="6.5" stroke-dasharray="2 1.4"/><circle cx="12" cy="12" r="10" stroke-dasharray="1.6 2"/></g></svg>SENSITIVITIES</div>
    <div class="nav" style="width:197px">
      <svg viewBox="0 0 24 24" fill="none" stroke="#222" stroke-width="1.8"><path d="M12 2.5l2.9 6.2 6.6.7-5 4.5 1.5 6.6L12 17.2l-6 3.3 1.5-6.6-5-4.5 6.6-.7z"/></svg>FAVOURITES</div>
  </header>

  <nav class="tabs">
    <div class="tab" style="left:70px;top:135px;width:140px;height:35px;line-height:36px">EQUITIES</div>
    <div class="tab" style="left:215px;top:135px;width:140px;height:35px;line-height:36px">ETFS</div>
    <div class="tab" style="left:360px;top:125px;width:140px;height:45px;line-height:45px">PAIRS</div>
    <div class="tab active" style="left:505px;top:115px;width:140px;height:55px;line-height:55px">ETF PAIRS</div>
    <div class="tab" style="left:650px;top:125px;width:140px;height:45px;line-height:45px">FACTORS</div>
    <div class="tab" style="left:795px;top:135px;width:140px;height:35px;line-height:36px">NEW TAB TITLE #1</div>
    <div class="tab" style="left:940px;top:135px;width:140px;height:35px;line-height:36px">NEW TAB TITLE #2</div>
    <div class="tab" style="left:1085px;top:135px;width:40px;height:35px;display:flex;align-items:center;justify-content:center">
      <svg width="14" height="20" viewBox="0 0 14 20" fill="none" stroke="#777" stroke-width="3"><path d="M3 2l8 8-8 8"/></svg></div>
    <div class="tab add" style="left:1130px;top:135px;width:100px;height:35px">
      <svg width="22" height="22" viewBox="0 0 22 22" fill="none" stroke="#fff" stroke-width="1.8"><circle cx="11" cy="11" r="9.5"/><path d="M11 6v10M6 11h10"/></svg>ADD</div>
  </nav>

  <div class="export">
    <svg width="26" height="24" viewBox="0 0 26 24" fill="none" stroke="#0b3768" stroke-width="2.2"><path d="M11 5H3v17h17v-7"/><path d="M8 16c1-6 6-10 14-10M17 2l5 4-5 4"/></svg>Export</div>

  <aside class="filters"><span>FILTERS</span></aside>
  <svg class="filters-arrow" width="30" height="30" viewBox="0 0 30 30"><circle cx="15" cy="15" r="13" fill="#0b3768" stroke="#fff" stroke-width="2"/><path d="M9 15h11M15 10l5 5-5 5" fill="none" stroke="#fff" stroke-width="2"/></svg>

  <table class="grid">
    <colgroup><col style="width:100px"><col style="width:140px"><col style="width:115px"><col style="width:85px"><col span="8" style="width:90px"></colgroup>
    <thead><tr>
      <th class="key">ID <svg width="11" height="8" viewBox="0 0 11 8" fill="none" stroke="#fff" stroke-width="2"><path d="M1 1.5l4.5 4.5L10 1.5"/></svg></th>
      <th class="key">Sector</th><th class="key">Time</th>
      <th class="stat">Quality</th><th class="stat">Stat 1</th><th class="stat">Stat 2</th><th class="stat">Stat 3</th><th class="stat">Stat 4</th><th class="stat">Stat 5</th><th class="stat">Stat 6</th><th class="stat">Stat 7</th><th class="stat">Stat 8</th>
    </tr></thead>
    <tbody>
      <tr><td>Model 1</td><td class="sector">Materials</td><td>2019-07-03<br>12:15:00.000</td><td class="num">30.2288</td><td class="num">2.01574</td><td class="num">23.305</td><td class="num">-0.149368</td><td class="num">22.3054</td><td class="num">4.63714</td><td class="num">0.945706</td><td class="num">2.81949</td><td class="num">2.60858</td></tr>
      <tr><td>Model 2</td><td class="sector">Industrials</td><td>2019-07-03<br>12:15:00.000</td><td class="num">32.8694</td><td class="num">0.87307</td><td class="num">32.185</td><td class="num">-0.033692</td><td class="num">33.9911</td><td class="num">11.5693</td><td class="num">-0.472968</td><td class="num">-0.830458</td><td class="num">6.80646</td></tr>
      <tr><td>Model 3</td><td class="sector">Consumer<br>Discretionary</td><td>2019-07-03<br>12:15:00.000</td><td class="num">1.66002</td><td class="num">-0.569222</td><td class="num">159.814</td><td class="num">0.0252328</td><td class="num">172.616</td><td class="num">10.2875</td><td class="num">-0.750396</td><td class="num">-0.385309</td><td class="num">4.69146</td></tr>
      <tr><td>Model 4</td><td class="sector">Information<br>Technology</td><td>2019-07-03<br>12:15:00.000</td><td class="num">45.6856</td><td class="num">0.412148</td><td class="num">202.488</td><td class="num">0.0084923</td><td class="num">205.834</td><td class="num">11.9094</td><td class="num">-0.137913</td><td class="num">0.449595</td><td class="num">3.85106</td></tr>
      <tr><td>Model 5</td><td class="sector">Information<br>Technology</td><td>2019-07-03<br>12:15:00.000</td><td class="num">75.7733</td><td class="num">7.06728</td><td class="num">188.605</td><td class="num">0.016913</td><td class="num">161.665</td><td class="num">3.82241</td><td class="num">0.981019</td><td class="num">1.29847</td><td class="num">3.34927</td></tr>
    </tbody>
  </table>
</div>
</body>
</html>
```